Oil and Gas Exploration and Production company needs a business card design

We need a business card design using our logo and colors in the logo. We want a mainstream design.

```html
<!DOCTYPE html>
<html lang="en">
<head>
<meta charset="utf-8">
<title>Condor Oil &amp; Gas – Business Card</title>
<link href="https://fonts.googleapis.com/css2?family=Arvo:wght@700&family=Source+Sans+3:wght@400;600;700&display=swap" rel="stylesheet">
<style>
  :root {
    --backdrop: #2b2b2d;
    --gold-light: #e9d64c;
    --gold-mid: #d4aa36;
    --gold-deep: #c8952b;
    --ink: #1c1a1b;
    --paper: #f7f7f5;
    --grey-text: #5d5d5d;
    --white: #ffffff;
  }
  * { margin: 0; padding: 0; box-sizing: border-box; }
  html, body { width: 1200px; height: 900px; overflow: hidden; }
  body {
    background: var(--backdrop);
    font-family: "Source Sans 3", "Helvetica Neue", Arial, sans-serif;
    display: flex;
    flex-direction: column;
    align-items: center;
    justify-content: center;
    gap: 50px;
  }
  .card {
    position: relative;
    width: 630px;
    height: 360px;
    overflow: hidden;
    box-shadow: 0 12px 30px rgba(0,0,0,0.45);
  }

  /* Back of card */
  .card-back {
    background: linear-gradient(100deg, var(--gold-light) 0%, var(--gold-mid) 45%, var(--gold-deep) 100%);
  }
  .back-brand {
    position: absolute;
    left: 0; right: 0; top: 120px;
    display: flex;
    align-items: center;
    justify-content: center;
    gap: 14px;
  }
  .brand-dot {
    width: 40px; height: 40px;
    border-radius: 50%;
    background: var(--ink);
    flex: none;
  }
  .back-brand .brand-name {
    font-family: "Arvo", Georgia, serif;
    font-weight: 700;
    font-size: 36px;
    color: var(--ink);
  }
  .web-address {
    position: absolute;
    left: 0; right: 0; bottom: 46px;
    text-align: center;
    color: var(--white);
    font-size: 15px;
    letter-spacing: 5px;
  }

  /* Front of card */
  .card-front { background: var(--paper); }
  .band {
    position: absolute;
    left: 0; right: 0;
    background: var(--gold-mid);
  }
  .band-main { top: 138px; height: 66px; }
  .band-thin { top: 262px; height: 18px; }
  .front-brand {
    position: absolute;
    left: 0; right: 0; top: 82px;
    display: flex;
    align-items: center;
    justify-content: center;
    gap: 10px;
  }
  .front-brand .brand-dot { width: 28px; height: 28px; }
  .front-brand .brand-name {
    font-family: "Arvo", Georgia, serif;
    font-weight: 700;
    font-size: 34px;
    color: var(--ink);
    line-height: 1;
  }
  .holder {
    position: absolute;
    left: 0; right: 0; top: 148px;
    text-align: center;
  }
  .holder-name {
    font-weight: 700;
    font-size: 20px;
    color: var(--ink);
    letter-spacing: 0.5px;
    line-height: 1.1;
  }
  .holder-title {
    font-size: 14px;
    color: var(--white);
    letter-spacing: 0.5px;
  }
  .address {
    position: absolute;
    right: 30px; top: 214px;
    text-align: right;
    font-size: 14px;
    line-height: 1.3;
    color: var(--grey-text);
  }
  .contacts {
    position: absolute;
    left: 26px; top: 287px;
    list-style: none;
    font-size: 13.5px;
    line-height: 16px;
    color: var(--grey-text);
  }
  .contacts li { display: flex; align-items: center; gap: 8px; }
  .contacts svg { width: 11px; height: 11px; fill: var(--ink); flex: none; }
</style>
</head>
<body>

  <section class="card card-back" aria-label="Card back">
    <div class="back-brand">
      <span class="brand-dot"></span>
      <span class="brand-name">Condor Oil &amp; Gas</span>
    </div>
    <p class="web-address">www.condoroilgas.com</p>
  </section>

  <section class="card card-front" aria-label="Card front">
    <div class="band band-main"></div>
    <div class="band band-thin"></div>

    <div class="front-brand">
      <span class="brand-dot"></span>
      <span class="brand-name">Condor Oil &amp; Gas</span>
    </div>

    <div class="holder">
      <p class="holder-name">DANIEL MARSH</p>
      <p class="holder-title">PRESIDENT</p>
    </div>

    <address class="address" style="font-style:normal">
      4120 Ridgeview Lane<br>
      Maple Glen, NY 11020
    </address>

    <ul class="contacts">
      <li>
        <svg viewBox="0 0 12 12" aria-hidden="true"><path d="M1 3.5C1 2 2.5 1 6 1s5 1 5 2.5V5H8.5V3.8H3.5V5H1Z M3 6h6l1.5 5h-9Z"/></svg>
        555 0142 2253
      </li>
      <li>
        <svg viewBox="0 0 12 12" aria-hidden="true"><path d="M3 0h6v12H3Z M4 1.5v8h4v-8Z"/></svg>
        555 0178 5335
      </li>
      <li>
        <svg viewBox="0 0 12 12" aria-hidden="true"><path d="M3 0h6v3H3Z M1 4h10v6H9v2H3v-2H1Z M4 8v3h4V8Z"/></svg>
        555 0196 3856
      </li>
      <li>
        <svg viewBox="0 0 12 12" aria-hidden="true"><path d="M0 2h12v1L6 7 0 3Z M0 4.2l6 4 6-4V10H0Z"/></svg>
        info@condoroilgas.com
      </li>
    </ul>
  </section>

</body>
</html>
```